Business Card Design For Office Furniture Clearance Company

Kestrel Office Clearance - our company name pretty much explains what we do, we clear offices for high end clients, mainly plc's and large international companies.

We require a nice looking business card that displays professionalism but without being too serious.

It would be nice to see just a little more than a conventional boring business card, make sure you add some flare.

Industry/Entity Type

Office Furniture

Contact Information for Business Card

CARD 1

Mark Holloway
Director
mark@kestrelofficeclearance.co.uk
m: 07700 153928

t: 01632 960418
www.kestrelofficeclearance.co.uk

Kestrel Office Clearance
Unit K4 B
2-8 Fenwick Lane
Halvercombe
Norlington Vale
ZZ9 4QT

free office clearances… you cant get better than that.

CARD 2

Peter Radford
Director
peter@kestrelofficeclearance.co.uk
m: 07700 382615

t: 01632 960418

Kestrel Office Clearance
Unit K4 B
2-8 Fenwick Lane
Halvercombe
Norlington Vale
ZZ9 4QT

Font styles to use
Sans Serif

Requirements
Must have
• A white background - as we have a blue logo.
Nice to have
• Nice use of the logo - play around with this and dissect it.

```html
<!DOCTYPE html>
<html lang="en">
<head>
<meta charset="utf-8">
<title>Kestrel Office Clearance – Business Card</title>
<link rel="stylesheet" href="https://fonts.googleapis.com/css2?family=Source+Sans+3:wght@400;600;700&display=swap">
<style>
  :root {
    --stage: #000000;
    --paper: #ffffff;
    --brand-blue: #0b6eb4;
    --deep-blue: #005b94;
    --ring-blue: #0a6fae;
    --ink: #1a1a1a;
    --reverse-text: #ffffff;
  }
  * { margin: 0; padding: 0; box-sizing: border-box; }
  html, body { width: 1200px; height: 900px; overflow: hidden; background: var(--stage); }
  body { position: relative; font-family: "Source Sans 3", "Myriad Pro", sans-serif; }

  .card { position: absolute; top: 275px; width: 477px; height: 293px; overflow: hidden; }
  .card-front { left: 116px; background: var(--paper); border-radius: 0 56px 0 56px; }
  .card-back { left: 622px; top: 276px; height: 292px; background: var(--deep-blue); border-radius: 56px 0 56px 0; }

  .brand-mark { position: absolute; left: 49px; top: 51px; width: 120px; height: 120px; border-radius: 50%; background: var(--brand-blue); }
  .brand-name-mark { position: absolute; left: 184px; top: 96px; font-size: 22px; font-weight: 600; color: var(--brand-blue); line-height: 1; }

  .person { position: absolute; right: 26px; top: 26px; text-align: right; }
  .person-name { font-size: 19.5px; font-weight: 600; color: var(--brand-blue); line-height: 24px; }
  .person-role { font-size: 14px; color: var(--ink); line-height: 16px; }

  .contact-list { position: absolute; right: 26px; top: 143px; list-style: none; }
  .contact-list li { display: flex; align-items: center; justify-content: flex-end; gap: 7px; font-size: 14px; color: var(--ink); height: 20px; }
  .contact-list svg { width: 11px; height: 11px; fill: var(--brand-blue); flex: none; }

  .company { position: absolute; right: 26px; top: 229px; text-align: right; }
  .company-name { font-size: 17.5px; font-weight: 600; color: var(--brand-blue); line-height: 22px; }
  .company-address { font-size: 14px; color: var(--ink); line-height: 20px; white-space: nowrap; }

  .back-ring { position: absolute; left: 96px; top: 2px; width: 286px; height: 286px; border-radius: 50%; background: var(--ring-blue); }
  .tagline { position: absolute; left: 0; right: 0; top: 93px; text-align: center; color: var(--reverse-text); font-size: 21px; font-weight: 600; line-height: 27px; letter-spacing: 0.2px; text-transform: uppercase; }
</style>
</head>
<body>
  <section class="card card-front" aria-label="Business card front">
    <div class="brand-mark"></div>
    <div class="brand-name-mark">Kestrel</div>

    <div class="person">
      <p class="person-name">Mark Holloway</p>
      <p class="person-role">Director</p>
    </div>

    <ul class="contact-list">
      <li>07700 153928
        <svg viewBox="0 0 12 12" aria-hidden="true"><path d="M3 0h6a1 1 0 0 1 1 1v10a1 1 0 0 1-1 1H3a1 1 0 0 1-1-1V1a1 1 0 0 1 1-1zm.5 1.5v8h5v-8z"/></svg>
      </li>
      <li>01632 960418
        <svg viewBox="0 0 12 12" aria-hidden="true"><path d="M2.4 0.5l2 2.2-1 1.4a7 7 0 0 0 4.5 4.5l1.4-1 2.2 2-1.3 1.9C5.6 11.8 0.2 6.4 0.5 1.8z"/></svg>
      </li>
      <li>mark@kestrelofficeclearance.co.uk
        <svg viewBox="0 0 12 12" aria-hidden="true"><path d="M0 2.5h12v7H0zM0.8 3.2L6 6.8l5.2-3.6v-.2H.8z" fill-rule="evenodd"/></svg>
      </li>
      <li>www.kestrelofficeclearance.co.uk
        <svg viewBox="0 0 12 12" aria-hidden="true"><circle cx="6" cy="6" r="6"/><path d="M3 3.5h3l-1 2 2 1-1 3-2-2zM7.5 2l2 1-1 1.5z" fill="#fff"/></svg>
      </li>
    </ul>

    <div class="company">
      <p class="company-name">Kestrel Office Clearance</p>
      <p class="company-address">Unit K4 B, 2-8 Fenwick Lane Halvercombe, Norlington Vale&nbsp; ZZ9 4QT</p>
    </div>
  </section>

  <section class="card card-back" aria-label="Business card back">
    <div class="back-ring"></div>
    <p class="tagline">Free office<br>clearances…<br>you cant get<br>better than that</p>
  </section>
</body>
</html>
```